Business Card Design

We have recently seen two business cards that caught our attention and think the designs would work for us. We are an accounting firm that serves small businesses in a variety of industries. Attached are the two business card that inspired us along with very rough layouts. We would like to see a professional layout using our company information.

Industry/Entity Type

Accounting

Contact Information for Business Card

Company Name - Marlowe Thistle
Address - 4182 Orlanby Lane, Suite 610, Houston, TX 77093
713-555-0187 - Main
281-555-0342 - Fax

Team Member Names, emails and phone numbers (see attachment)

```html
<!DOCTYPE html>
<html lang="en">
<head>
<meta charset="utf-8">
<title>Marlowe Thistle – Business Card</title>
<link href="https://fonts.googleapis.com/css2?family=Lato:wght@400;700;900&display=swap" rel="stylesheet">
<style>
  :root {
    --backdrop: #2a2a2a;
    --card-light: #ffffff;
    --card-shade: #e4e4e4;
    --ink: #111111;
    --ink-soft: #2b2b2b;
    --muted: #a6a6a6;
    --rule: #1a1a1a;
  }
  * { margin: 0; padding: 0; box-sizing: border-box; }
  html, body {
    width: 1200px; height: 900px; overflow: hidden;
    background: var(--backdrop);
    font-family: "Lato", Arial, sans-serif;
    color: var(--ink);
  }
  .business-card {
    position: absolute; left: 100px; top: 160px;
    width: 1000px; height: 580px;
    border-radius: 36px;
    background: linear-gradient(125deg, var(--card-shade) 0%, var(--card-light) 45%, var(--card-light) 70%, var(--card-shade) 100%);
    box-shadow: 0 20px 50px rgba(0,0,0,.5);
  }
  .contact-person {
    position: absolute; right: 70px; top: 70px;
    text-align: right;
  }
  .person-name {
    font-weight: 900; font-size: 42px; letter-spacing: 1px;
    text-transform: uppercase; line-height: 1;
  }
  .name-rule { display: block; margin: 6px 0 4px auto; }
  .person-title {
    font-size: 24px; color: var(--muted); letter-spacing: 1px;
    text-transform: uppercase; line-height: 1.1;
  }
  .detail-line {
    display: flex; align-items: center; justify-content: flex-end; gap: 10px;
    font-size: 26px; font-weight: 700; color: var(--ink-soft); margin-top: 8px;
  }
  .detail-line.email { margin-top: 36px; }
  .brand-mark {
    position: absolute; left: 110px; top: 230px;
    display: flex; align-items: center; gap: 18px;
  }
  .brand-square { width: 56px; height: 56px; background: var(--ink); }
  .brand-name {
    font-weight: 900; font-size: 34px; letter-spacing: 2px;
    text-transform: uppercase;
  }
  .company-block {
    position: absolute; left: 300px; top: 372px;
  }
  .company-name {
    font-weight: 900; font-size: 46px; letter-spacing: 1px;
    text-transform: uppercase; line-height: 1;
  }
  .company-row {
    display: flex; align-items: center; gap: 12px;
    font-size: 28px; font-weight: 700; color: var(--ink-soft); margin-top: 14px;
  }
  .company-row .spacer { width: 30px; }
  .icon { width: 28px; height: 28px; fill: var(--ink); flex: none; }
</style>
</head>
<body>
  <div class="business-card">
    <div class="contact-person">
      <div class="person-name">Delphine Arbor</div>
      <svg class="name-rule" width="400" height="8" viewBox="0 0 400 8">
        <path d="M0 7 L400 1 L400 5 Z" fill="var(--rule)"/>
      </svg>
      <div class="person-title">Account Manager</div>
      <div class="detail-line phone">
        <svg class="icon" viewBox="0 0 24 24"><path d="M7 1h10a2 2 0 0 1 2 2v18a2 2 0 0 1-2 2H7a2 2 0 0 1-2-2V3a2 2 0 0 1 2-2zm0 3v15h10V4z"/></svg>
        <span>832-555-0129</span>
      </div>
      <div class="detail-line email">
        <svg class="icon" viewBox="0 0 24 24"><path d="M2 5h20v14H2zm2 2v.5l8 5.5 8-5.5V7zm0 3v7h16v-7l-8 5.5z"/></svg>
        <span>darbor@marlowethistle.com</span>
      </div>
    </div>

    <div class="brand-mark">
      <div class="brand-square"></div>
      <div class="brand-name">Marlowe Thistle</div>
    </div>

    <div class="company-block">
      <div class="company-name">Marlowe Thistle</div>
      <div class="company-row">
        <svg class="icon" viewBox="0 0 24 24"><path d="M2 8c0-2 3-4 10-4s10 2 10 4v2h-5V8H7v2H2zm4 4h12l3 8H3zm6 2a3 3 0 1 0 0 6 3 3 0 0 0 0-6z"/></svg>
        <span>713-555-0187</span>
        <span class="spacer"></span>
        <svg class="icon" viewBox="0 0 24 24"><path d="M6 2h10l2 2v5H6zm-3 8h18a1 1 0 0 1 1 1v7h-4v4H6v-4H2v-7a1 1 0 0 1 1-1zm5 7v3h8v-3z"/></svg>
        <span>281-555-0342</span>
      </div>
      <div class="company-row">
        <svg class="icon" viewBox="0 0 24 24"><path d="M12 3l10 9h-3v9h-5v-6h-4v6H5v-9H2z"/></svg>
        <span>4182 Orlanby Lane, Suite 610, Houston, TX 77093</span>
      </div>
    </div>
  </div>
</body>
</html>
```